Media Services Start-up -- Corporate Website and Logo Design. Inspiration required!

We need a logo design and corporate website design, including coding, for our start-up business.
Vennatra’s value proposition is based on bringing together media content from a vast number of geographies globally, adding human and AI curation, translation and editing, and delivering the content using tailored customer interfaces. On the one hand, the business brings together media coverage from all over the world, and on the other it brings together content, human skills and technology to deliver a supreme customer experience.
Vennatra is a B2B media monitoring and analytics business with emphasis on global customers. Vennatra's service offering is centred around sourcing media content from different markets, processing, storing and delivering the content and insights derived from it using an online platform / mobile app.
The messaging we want to create through the logo is:
- Global scope
- Speed of delivery
- Cost-efficiency
- Multi-lingual
- Tailor-made
- Trustworthy
Target Market(s)
Business to business, PR / Communications, Media, Marketing
Logo Text
Vennatra
Coding
Coded - Design and coding required
Number of Pages Required
5+ page
Font styles to use
Other font styles liked:
- See Design Brief for details
Colors
Designer to choose colors to be used in the design.

```html
<!DOCTYPE html>
<html lang="en">
<head>
<meta charset="utf-8">
<title>Vennatra – Our Solutions</title>
<link href="https://fonts.googleapis.com/css2?family=Roboto:wght@400;500;700&display=swap" rel="stylesheet">
<style>
:root{
  --teal:#3aaf9f;
  --teal-line:#2f9e8e;
  --ink:#5a5a5a;
  --nav:#666;
  --white:#fff;
  --hero-dark:#0b0b0b;
}
*{margin:0;padding:0;box-sizing:border-box}
html,body{width:1200px;height:748px;overflow:hidden;background:#000}
body{font-family:'Roboto',sans-serif;position:relative}
.site-header{position:absolute;left:0;top:0;width:1200px;height:85px;background:var(--white)}
.brand{position:absolute;left:141px;top:12px;font-size:50px;font-weight:700;color:var(--ink);letter-spacing:-0.5px}
.contact{position:absolute;top:10px;display:flex;align-items:center;gap:8px;font-size:14px;color:var(--nav)}
.contact svg{width:27px;height:27px}
.contact.phone{left:733px}
.contact.email{left:899px}
.main-nav{position:absolute;top:54px;font-size:14.5px;color:var(--nav)}
.main-nav span{position:absolute;white-space:nowrap}
.sign-in{position:absolute;left:974px;top:49px;width:85px;height:29px;background:var(--teal);color:var(--white);font-size:15px;display:flex;align-items:center;justify-content:center;letter-spacing:.3px}
.hero{position:absolute;left:0;top:85px;width:1200px;height:627px;overflow:hidden}
.hero-bg{position:absolute;inset:0;background:
  radial-gradient(circle at 600px 250px,#3a3a3a 0,#262626 120px,#141414 300px,#070707 560px),var(--hero-dark)}
.hero-title{position:absolute;top:52px;width:100%;text-align:center;color:var(--white);font-size:32px;font-weight:700}
.hero-lead{position:absolute;top:108px;width:100%;text-align:center;color:var(--white);font-size:14px;font-weight:700;line-height:20px}
.tab{position:absolute;top:182px;transform:translateX(-50%);text-align:center;color:var(--white);font-size:15.5px;white-space:nowrap;letter-spacing:.2px}
.tab svg{display:block;margin:0 auto 6px;width:30px;height:30px}
.tab.active{font-weight:700}
.tab-rule{position:absolute;left:162px;top:249px;width:876px;height:2px;background:#d8d8d8}
.tab-rule .marker{position:absolute;left:317px;top:-1px;width:165px;height:3px;background:var(--teal)}
.features{position:absolute;left:148px;top:307px;list-style:none;color:var(--white);font-size:12.7px;line-height:19px;width:440px}
.features li{position:relative;padding-left:14px;margin-bottom:7px;padding-left:14px}
.features li svg{position:absolute;left:0;top:4px;width:11px;height:11px}
.features li span{display:block;margin-left:0}
.feature-frame{position:absolute;left:624px;top:322px;width:422px;height:260px;border:1px solid var(--teal-line)}
.feature-visual{position:absolute;left:636px;top:308px;width:423px;height:260px;
  background:linear-gradient(100deg,#c2391f 0%,#3b2a6e 30%,#1b3f7a 55%,#1fa6a0 80%,#0b2b4f 100%)}
.slider-arrow{position:absolute;top:411px;width:32px;height:32px;border:1px solid #ccc;display:flex;align-items:center;justify-content:center}
.slider-arrow svg{width:14px;height:18px}
.slider-arrow.prev{left:93px}
.slider-arrow.next{left:1076px}
.site-footer{position:absolute;left:0;top:712px;width:1200px;height:36px;background:var(--teal);color:var(--white)}
.copyright{position:absolute;left:141px;top:10px;font-size:13px}
.social{position:absolute;left:996px;top:11px;display:flex;gap:9px}
.social span{width:14px;height:14px;border-radius:50%;background:var(--white)}
</style>
</head>
<body>
<header class="site-header">
  <div class="brand">Vennatra</div>
  <div class="contact phone">
    <svg viewBox="0 0 28 28"><circle cx="14" cy="14" r="13" fill="none" stroke="#3aaf9f" stroke-width="1.2"/><path d="M10 8c1 0 2 2 2 3s-1 1-1 2 3 4 4 4 1-1 2-1 3 1 3 2-1 2-2 2c-4 0-10-6-10-10 0-1 1-2 2-2z" fill="#666"/></svg>
    <span>+1 555 014 2290</span>
  </div>
  <div class="contact email">
    <svg viewBox="0 0 28 28"><circle cx="14" cy="14" r="13" fill="none" stroke="#3aaf9f" stroke-width="1.2"/><rect x="8" y="10" width="12" height="8" fill="none" stroke="#666" stroke-width="1.3"/><path d="M8 10l6 5 6-5" fill="none" stroke="#666" stroke-width="1.3"/></svg>
    <span>info@vennatra.com</span>
  </div>
  <nav class="main-nav">
    <span style="left:498px">Home</span>
    <span style="left:562px">Solutions</span>
    <span style="left:648px">How We Do It</span>
    <span style="left:760px">Our People</span>
    <span style="left:856px">Our Technology</span>
  </nav>
  <div class="sign-in">SIGN IN</div>
</header>

<section class="hero">
  <div class="hero-bg" role="img" aria-label="Dark night city skyline with a globe and network lines and faint circular service icons"></div>
  <h1 class="hero-title">Our Solutions</h1>
  <p class="hero-lead">Lorem ipsum dolor sit amet, consectetuer adipiscing elit, sed diam nonummy nibh<br>euismod tincidunt ut laoreet dolore magna aliquam erat volutpat.</p>

  <div class="tab" style="left:227px"><svg viewBox="0 0 30 30"><rect x="4" y="12" width="10" height="8" fill="none" stroke="#fff" stroke-width="1.5"/><rect x="18" y="14" width="7" height="10" fill="none" stroke="#fff" stroke-width="1.5"/><path d="M10 9a4 4 0 0 1 8 0h2a3 3 0 0 1 0 4" fill="none" stroke="#fff" stroke-width="1.5"/></svg>Content Sourcing</div>
  <div class="tab" style="left:385px"><svg viewBox="0 0 30 30"><path d="M7 15a5 5 0 0 1 3-9 7 7 0 0 1 12 2 4 4 0 0 1 1 7z" fill="#fff"/><rect x="8" y="18" width="14" height="3" fill="#fff"/><rect x="8" y="23" width="14" height="3" fill="#fff"/></svg>Content Collection</div>
  <div class="tab active" style="left:563px"><svg viewBox="0 0 30 30"><circle cx="15" cy="10" r="4" fill="#3aaf9f"/><path d="M9 26c0-7 3-10 6-10s6 3 6 10z" fill="#3aaf9f"/><path d="M3 3l8 8M27 3l-8 8M3 27l7-7M27 27l-7-7" stroke="#3aaf9f" stroke-width="1.5"/></svg>Content Augmentation</div>
  <div class="tab" style="left:732px"><svg viewBox="0 0 30 30"><circle cx="15" cy="15" r="6" fill="none" stroke="#fff" stroke-width="1.5"/><g fill="#fff"><circle cx="15" cy="3" r="2"/><circle cx="15" cy="27" r="2"/><circle cx="3" cy="15" r="2"/><circle cx="27" cy="15" r="2"/><circle cx="6" cy="6" r="2"/><circle cx="24" cy="24" r="2"/><circle cx="24" cy="6" r="2"/><circle cx="6" cy="24" r="2"/></g></svg>Content Delivery</div>
  <div class="tab" style="left:927px"><svg viewBox="0 0 30 30"><circle cx="10" cy="16" r="3.5" fill="#fff"/><path d="M3 27c0-5 3-7 7-7s7 2 7 7z" fill="#fff"/><path d="M16 12a4 4 0 0 1 3-7 5 5 0 0 1 9 2 3 3 0 0 1-1 6z" fill="#fff"/></svg>Media Insights &amp; Consultancy</div>
  <div class="tab-rule"><div class="marker"></div></div>

  <ul class="features">
    <li><svg viewBox="0 0 12 12"><circle cx="6" cy="6" r="6" fill="#fff"/><path d="M3 6l2 2 4-4" fill="none" stroke="#000" stroke-width="1.5"/></svg><span>We manage and normalise all of the source-level reference data -<br>country, language, reach etc.</span></li>
    <li><svg viewBox="0 0 12 12"><circle cx="6" cy="6" r="6" fill="#fff"/><path d="M3 6l2 2 4-4" fill="none" stroke="#000" stroke-width="1.5"/></svg><span>We add editorial validation to ensure only the content required reaches<br>your delivery, removing inevitable noise from source providers</span></li>
    <li><svg viewBox="0 0 12 12"><circle cx="6" cy="6" r="6" fill="#fff"/><path d="M3 6l2 2 4-4" fill="none" stroke="#000" stroke-width="1.5"/></svg><span>Tagging - AI and human based tagging to detect locations, people,<br>topics, products, brands, services, etc.</span></li>
    <li><svg viewBox="0 0 12 12"><circle cx="6" cy="6" r="6" fill="#fff"/><path d="M3 6l2 2 4-4" fill="none" stroke="#000" stroke-width="1.5"/></svg><span>Human and automated grouping of stories across geographies -<br>clustering, "also-in" groupings etc.</span></li>
    <li><svg viewBox="0 0 12 12"><circle cx="6" cy="6" r="6" fill="#fff"/><path d="M3 6l2 2 4-4" fill="none" stroke="#000" stroke-width="1.5"/></svg><span>Translation summarisation - AI Translation or human-created<br>depending on budget, speed of delivery and need.</span></li>
    <li><svg viewBox="0 0 12 12"><circle cx="6" cy="6" r="6" fill="#fff"/><path d="M3 6l2 2 4-4" fill="none" stroke="#000" stroke-width="1.5"/></svg><span>Digest authoring - refining the essence of today’s coverage into a<br>concise board-ready output for your organisation</span></li>
  </ul>

  <div class="feature-frame"></div>
  <div class="feature-visual" role="img" aria-label="Digital globe with glowing data streams and hexagonal technology icons"></div>

  <div class="slider-arrow prev"><svg viewBox="0 0 14 18"><path d="M11 1L3 9l8 8" fill="none" stroke="#fff" stroke-width="1.5"/></svg></div>
  <div class="slider-arrow next"><svg viewBox="0 0 14 18"><path d="M3 1l8 8-8 8" fill="none" stroke="#fff" stroke-width="1.5"/></svg></div>
</section>

<footer class="site-footer">
  <p class="copyright">Copyright © 2019 Vennatra. All Rights Reserved.</p>
  <div class="social"><span></span><span></span><span></span></div>
</footer>
</body>
</html>
```